Veltra Metrics New Website for Health Benefits Plan Decisioneering Tool Launch

Veltra Metrics is a SaaS provider of health benefits comparison tools. We need a new simple SaaS focused website to direct customers to our product

Target Market(s)

General Public comparing their health benefits plans from their employer or from the state exchanges in the US

Coding

Coded - Design and coding required

Number of Pages Required

3 page

Requirements
Must have
• Main page - "Know the Best Health Benefits Plan for You!"
Graphic of a person looking over papers on their desk
Compare Now button to link to SaaS product
About Us
Product Page

https://plimbo.example/top-app-pages/

```html
<!DOCTYPE html>
<html lang="en">
<head>
<meta charset="UTF-8">
<title>Veltra Metrics — Know the Best Health Benefits Plan for You</title>
<link rel="stylesheet" href="https://fonts.googleapis.com/css2?family=Cinzel:wght@400;600&family=Montserrat:wght@400;500&display=swap">
<style>
  :root {
    --page-bg: #eef7fd;
    --brand-blue: #29a9e1;
    --footer-blue: #29abe2;
    --nav-ink: #1a1a1a;
    --white: #ffffff;
    --art-light: #cfe8f7;
    --art-mid: #8fb3de;
  }
  * { box-sizing: border-box; margin: 0; padding: 0; }
  html, body { width: 1200px; height: 576px; overflow: hidden; }
  body {
    background: var(--page-bg);
    font-family: "Montserrat", sans-serif;
    position: relative;
  }
  .site-header {
    position: absolute; top: 0; left: 0; width: 1200px; height: 100px;
  }
  .brand-name {
    position: absolute; left: 162px; top: 42px;
    font-family: "Cinzel", serif; font-weight: 400;
    font-size: 29px; letter-spacing: 0.5px;
    color: var(--brand-blue); text-decoration: none; white-space: nowrap;
  }
  .main-nav { position: absolute; top: 51px; left: 742px; display: flex; gap: 39px; }
  .main-nav a {
    font-size: 13.5px; font-weight: 500; color: var(--nav-ink);
    text-decoration: none; letter-spacing: 0.2px;
  }
  .hero-copy { position: absolute; left: 164px; top: 222px; }
  .hero-title {
    font-family: "Cinzel", serif; font-weight: 600;
    font-size: 40px; line-height: 51px; color: var(--brand-blue);
    letter-spacing: 1px;
  }
  .compare-button {
    position: absolute; left: -3px; top: 169px;
    width: 188px; height: 45px; border-radius: 23px;
    background: var(--brand-blue); color: var(--white);
    font-size: 15px; font-weight: 500; letter-spacing: 0.3px;
    display: flex; align-items: center; justify-content: center;
    text-decoration: none;
  }
  .hero-art {
    position: absolute; left: 667px; top: 105px; width: 458px; height: 426px;
    background: linear-gradient(160deg, var(--art-light) 0%, var(--art-mid) 100%);
    border-radius: 10px;
  }
  .site-footer {
    position: absolute; left: 0; bottom: 0; width: 1200px; height: 45px;
    background: var(--footer-blue); color: var(--white);
    font-size: 13.5px; display: flex; align-items: center; justify-content: center;
  }
</style>
</head>
<body>
  <header class="site-header">
    <a class="brand-name" href="#">VELTRA METRICS</a>
    <nav class="main-nav">
      <a href="#">HOME</a>
      <a href="#">ABOUT US</a>
      <a href="https://plimbo.example/top-app-pages/">PRODUCT PAGE</a>
    </nav>
  </header>

  <main>
    <section class="hero-copy">
      <h1 class="hero-title">Know the Best<br>Health Benefits<br>Plan for You!</h1>
      <a class="compare-button" href="https://plimbo.example/top-app-pages/">COMPARE NOW</a>
    </section>
    <div class="hero-art" role="img" aria-label="Illustration of two people at a desk reviewing papers and a laptop"></div>
  </main>

  <footer class="site-footer">Copyright © 2020 VELTRA METRICS. All Rights Reserved.</footer>
</body>
</html>
```